"Tandem Mouthguards " Custom-made Mouthguard Business Website

We need an informational website for our mouthguard Business "Tandem Mouthguards". The logo is navy blue/lime green so want to have colour scheme that goes nicely with this - have uploaded our mouthguard flyer with some information we need to put into the website but I do have more information to put in there.

Target Market(s)

Sports clubs, sportspeople, parents and kids, schools

Industry/Entity Type

Dental, Custom-made Sports Mouthguards

Coding

Coded - Design and coding required

Number of Pages Required

5+ page

Font styles to use
Serif
Sans Serif

Colors
0054AA
0677BA
7BADD7
CADEEF
E8F1F8
0094D4
00A9DD
6FCCEA
C7EBF8
E9F6FB
00AB8E
00BBA5
67D7C9
C6EFE9
E9F9F6
59FF00
82FF00
B8FF75
E3FFCB
F4FFEA
FFF300
FFF600
FEFA6F
FFFEC7
FFFEE8
FFC000
F8CF3A
FAE287
FDF2CF
FEFAEE
F0912C
F2A743
F7CA91
FBE8D2
FDF5EE
EE7325
F08F49
F5BC92
FAE3D3
FDF4ED

Requirements
Must have
• I want drop down pages, not one scrolling page. Different pages for each heading . Content uploaded - We need a general home page with lots of pictures and info that I'll provide. A page each dedicated to 1) About Us 2) Why choose a custom mouthguard? 3) Gallery 4) Contact Us. Will need logos from "Velora"
Nice to have
• Mainly use greens and blues, but happy to pop in some yellow/oranges/red oranges if it looks good

```html
<!DOCTYPE html>
<html lang="en">
<head>
<meta charset="utf-8">
<title>Tandem Mouthguards – Custom-Made Sports Mouthguards</title>
<link href="https://fonts.googleapis.com/css2?family=Montserrat:wght@400;500;600;700;800&display=swap" rel="stylesheet">
<style>
:root{
  --navy:#14307e;
  --blue:#00a9dd;
  --blue-deep:#0094d4;
  --teal:#00bba5;
  --green:#37c84a;
  --lime:#59d43a;
  --ink:#2b2b2b;
  --muted:#555;
  --line:#e3e3e3;
  --white:#fff;
}
*{margin:0;padding:0;box-sizing:border-box}
html,body{width:1200px;height:4121px;overflow:hidden}
body{font-family:"Montserrat",sans-serif;color:var(--ink);background:var(--white);position:relative}
.abs{position:absolute}

/* header */
.site-header{position:absolute;left:0;top:0;width:1200px;height:118px;background:#fff}
.brand{position:absolute;display:flex;align-items:center;gap:10px;color:var(--navy);font-weight:800;line-height:1}
.brand-dot{width:18px;height:18px;border-radius:50%;background:var(--lime);flex:none}
.brand-name{font-size:22px;letter-spacing:.5px;text-transform:uppercase}
.site-header .brand{left:91px;top:38px}
.nav{position:absolute;top:45px;left:0;font-size:15px;font-weight:500;color:#333}
.nav a{position:absolute;white-space:nowrap;text-decoration:none;color:inherit}
.nav .active{color:var(--green);font-weight:700}
.btn-start{position:absolute;left:925px;top:32px;width:184px;height:50px;border-radius:25px;
  background:linear-gradient(90deg,var(--blue),var(--green));color:#fff;font-size:15px;font-weight:600;
  display:flex;align-items:center;justify-content:center}

/* hero */
.hero{position:absolute;left:0;top:118px;width:1200px;height:546px;
  background:linear-gradient(100deg,#04a4e0 0%,#1ab7b4 45%,#3ccf3e 100%);overflow:hidden}
.hero-title{position:absolute;left:112px;top:84px;font-size:38px;font-weight:800;line-height:50px;color:#fff;text-transform:uppercase}
.hero-title .first{color:var(--navy)}
.hero-rule{position:absolute;left:112px;top:246px;width:405px;height:3px;background:rgba(255,255,255,.85)}
.hero-sub{position:absolute;left:112px;top:276px;width:430px;font-size:20px;line-height:28px;color:#fff;font-weight:500}
.btn-outline{position:absolute;left:112px;top:368px;width:173px;height:50px;border:2px solid #fff;border-radius:25px;
  color:#fff;font-size:16px;font-weight:500;display:flex;align-items:center;justify-content:center}
.hero-photo{position:absolute;left:530px;top:40px;width:660px;height:500px;border-radius:40px 40px 0 0;
  background:linear-gradient(135deg,rgba(120,60,200,.55),rgba(240,200,40,.55) 55%,rgba(40,60,170,.55))}
.hero-wave{position:absolute;left:0;top:600px;width:1200px;height:80px}

/* section headings */
.sec-title{position:absolute;left:0;width:1200px;text-align:center;font-size:35px;font-weight:700;color:#2a2a2a;text-transform:uppercase}
.sec-rule{position:absolute;height:4px;background:var(--green)}
.on-color .sec-title{color:#fff}

/* feature cards */
.card{position:absolute;background:#fff;border:2px solid var(--line);border-radius:12px;text-align:center;padding:0 22px}
.card.featured{background:linear-gradient(135deg,var(--green),var(--blue));border-color:transparent}
.card .icon{width:92px;height:92px;border-radius:50%;margin:28px auto 0;background:linear-gradient(135deg,var(--blue-deep),var(--teal));
  display:flex;align-items:center;justify-content:center}
.card.featured .icon{background:#fff}
.card h3{font-size:20px;font-weight:600;margin-top:22px;color:#2a2a2a}
.card p{font-size:13.5px;line-height:21px;color:var(--muted);margin-top:12px}
.card.featured h3,.card.featured p{color:#fff}

/* about */
.about{position:absolute;left:0;top:1627px;width:1200px;height:629px;background:linear-gradient(180deg,#12b4a3,#08a2dc)}
.about-photo{position:absolute;left:114px;top:88px;width:486px;height:467px;border-radius:10px;
  background:radial-gradient(circle at 50% 40%,#f2e2a0 0%,#e8eef4 40%,#f7f7f7 75%)}
.about h2{position:absolute;left:634px;top:96px;font-size:35px;font-weight:700;color:#fff}
.about .rule{position:absolute;left:634px;top:157px;width:155px;height:4px;background:#fff}
.about-text{position:absolute;left:634px;top:188px;width:440px;font-size:15.5px;line-height:27.3px;color:#fff}
.about-text p+p{margin-top:27px}

/* gallery */
.thumb{position:absolute;top:2491px;width:218px;height:229px;border-radius:8px}
.arrow{position:absolute;top:2589px;width:32px;height:32px}

/* mouthguards */
.guards{position:absolute;left:0;top:2832px;width:1200px;height:765px;background:linear-gradient(135deg,#06a6df,#13b6a2)}
.guards .kicker{position:absolute;left:0;top:194px;width:1200px;text-align:center;color:#fff;font-size:17px;font-weight:600;text-transform:uppercase}
.guards .intro{position:absolute;left:190px;top:236px;width:820px;text-align:center;color:#fff;font-size:17px;line-height:27px}

/* footer */
.site-footer .brand{left:112px;top:3720px}
.contact-line{position:absolute;left:112px;display:flex;align-items:center;gap:10px;font-size:16px;color:#333}
.links-title{position:absolute;left:578px;top:3716px;font-size:18px;font-weight:700;color:var(--navy)}
.links-rule{position:absolute;left:578px;top:3748px;width:80px;height:3px;background:var(--green)}
.link{position:absolute;left:578px;font-size:15.5px;color:#333}
.partner{position:absolute;left:832px;width:256px;text-align:center;font-weight:800;line-height:1}
.copyright{position:absolute;left:0;top:4088px;width:1200px;height:33px;background:linear-gradient(90deg,#12b69c,#3cc84a);
  color:#fff;font-size:13px;display:flex;align-items:center;justify-content:center}
</style>
</head>
<body>

<header class="site-header">
  <div class="brand"><span class="brand-dot"></span><span class="brand-name">Tandem<br>Mouthguards</span></div>
  <nav class="nav">
    <a class="active" style="left:333px">HOME</a>
    <a style="left:424px">ABOUT US</a>
    <a style="left:547px">OUR MOUTHGUARD</a>
    <a style="left:747px">GALLERY</a>
    <a style="left:861px">FAQ</a>
  </nav>
  <div class="btn-start">GET STARTED</div>
</header>

<section class="hero">
  <div class="hero-photo" role="img" aria-label="Two young footballers in club jerseys holding a football and wearing coloured mouthguards"></div>
  <h1 class="hero-title"><span class="first">Tandem Mouthguards</span><br>Custom-made sports<br>mouthguards in</h1>
  <div class="hero-rule"></div>
  <p class="hero-sub">Protect your smile with a comfortable, professional fit.</p>
  <div class="btn-outline">BOOK NOW</div>
</section>
<svg class="hero-wave" viewBox="0 0 1200 80" preserveAspectRatio="none">
  <path d="M0 18 C300 40 700 60 1200 22 L1200 80 L0 80 Z" fill="#fff"/>
  <path d="M0 18 C300 40 700 60 1200 22 L1200 30 C700 72 300 52 0 24 Z" fill="#1c8fe0"/>
</svg>

<!-- why choose us -->
<h2 class="sec-title" style="top:760px">Why Choose Us</h2>
<div class="sec-rule" style="left:493px;top:833px;width:211px"></div>

<div class="card featured" style="left:114px;top:898px;width:275px;height:273px">
  <div class="icon"><svg width="50" height="50" viewBox="0 0 50 50"><circle cx="25" cy="20" r="14" fill="none" stroke="#0aa6d8" stroke-width="4"/><path d="M25 12l2.6 5.3 5.8.8-4.2 4.1 1 5.8-5.2-2.7-5.2 2.7 1-5.8-4.2-4.1 5.8-.8z" fill="#0aa6d8"/><path d="M15 31l-4 12 6-3 3 5 3-11M35 31l4 12-6-3-3 5-3-11" fill="#0aa6d8"/></svg></div>
  <h3>Professionally Made</h3>
  <p>Crafted by a qualified dental prosthetist with over 20 years of experience.</p>
</div>
<div class="card" style="left:462px;top:898px;width:277px;height:273px">
  <div class="icon"><svg width="54" height="54" viewBox="0 0 54 54" fill="none" stroke="#fff" stroke-width="3.5"><circle cx="27" cy="27" r="16"/><circle cx="27" cy="27" r="9"/><path d="M27 4v8M27 42v8M4 27h8M42 27h8"/></svg></div>
  <h3>Perfect Custom Fit</h3>
  <p>Designed to match your teeth and bite for maximum comfort and protection.</p>
</div>
<div class="card" style="left:811px;top:898px;width:277px;height:273px">
  <div class="icon"><svg width="54" height="54" viewBox="0 0 54 54" fill="none" stroke="#fff" stroke-width="3.5" stroke-linejoin="round"><path d="M27 6l12 5v9c0 7-5 12-12 14-7-2-12-7-12-14v-9z"/><path d="M8 36l10 10h10l8-6 10-8"/></svg></div>
  <h3>Durable &amp; Reliable</h3>
  <p>Made from high-quality dental materials that last longer than chemist-bought options.</p>
</div>

<div class="card" style="left:114px;top:1224px;width:277px;height:274px">
  <div class="icon"><svg width="56" height="50" viewBox="0 0 56 50" fill="#fff"><circle cx="28" cy="12" r="7"/><circle cx="13" cy="17" r="5.5"/><circle cx="43" cy="17" r="5.5"/><path d="M18 42c0-10 4-18 10-18s10 8 10 18z"/><path d="M4 42c0-8 3-14 9-14 2 0 4 1 5 2-2 3-3 7-3 12zM52 42c0-8-3-14-9-14-2 0-4 1-5 2 2 3 3 7 3 12z"/></svg></div>
  <h3>Styles for Everyone</h3>
  <p>Choose from nearly 40 colours, stripes, marbled effects, glitter, or team patterns.</p>
</div>
<div class="card" style="left:463px;top:1224px;width:277px;height:274px">
  <div class="icon"><svg width="56" height="56" viewBox="0 0 56 56" fill="#fff"><circle cx="40" cy="10" r="5"/><rect x="35" y="17" width="10" height="30" rx="4"/><circle cx="26" cy="20" r="4"/><rect x="22" y="26" width="8" height="21" rx="3"/><circle cx="14" cy="28" r="3"/><rect x="11" y="33" width="6" height="14" rx="2.5"/></svg></div>
  <h3>Kids, Teens &amp; Adults</h3>
  <p>From junior athletes to professionals, we create mouthguards for every age and</p>
</div>
<div class="card" style="left:812px;top:1224px;width:277px;height:274px">
  <div class="icon"><svg width="54" height="54" viewBox="0 0 54 54" fill="none" stroke="#fff" stroke-width="3.5" stroke-linejoin="round"><rect x="14" y="10" width="22" height="30" rx="3"/><path d="M8 44l8-10h12l6 6"/><circle cx="38" cy="20" r="7" fill="#fff"/><path d="M35 20l2 2 4-4" stroke="#0aa6d8" stroke-width="2.5"/></svg></div>
  <h3>Convenient Access</h3>
  <p>Book at our Kelso clinic, or take advantage of mobile school and club visits.</p>
</div>

<!-- about -->
<section class="about">
  <div class="about-photo" role="img" aria-label="Collage of athletes in action: rugby, ice hockey, soccer and volleyball players"></div>
  <h2>ABOUT US</h2>
  <div class="rule"></div>
  <div class="about-text">
    <p>My name is Lena Hartwell, and I am the dental prosthetist behind <b>Tandem Mouthguards.</b> With over 20 years of experience in the dental field, I am passionate about protecting smiles and helping athletes of all ages play with confidence.</p>
    <p>At <b>Coastal Denture Studio</b> in Kelso, I design and make <b>custom-fitted sports mouthguards</b> that are tailored to each individual's teeth and bite. Every mouthguard is crafted with precision so it fits comfortably, feels secure, and provides maximum protection on the field, court, or in the ring.</p>
  </div>
</section>

<!-- gallery -->
<h2 class="sec-title" style="top:2352px">Our Gallery</h2>
<div class="sec-rule" style="left:517px;top:2422px;width:157px"></div>
<svg class="arrow" style="left:55px" viewBox="0 0 32 32" fill="none" stroke="#333" stroke-width="2"><circle cx="16" cy="16" r="14"/><path d="M10 16h12M17 11l5 5-5 5"/></svg>
<div class="thumb" style="left:114px;background:linear-gradient(135deg,#8a6bd0,#c7b8ea)" role="img" aria-label="Purple glitter mouthguard held in a hand"></div>
<div class="thumb" style="left:366px;background:linear-gradient(135deg,#52c86a,#e8ece9)" role="img" aria-label="White mouthguard with team emblem in a green case"></div>
<div class="thumb" style="left:619px;background:linear-gradient(135deg,#d95cc4,#3a5bd8)" role="img" aria-label="Blue glitter mouthguard on a pink background"></div>
<div class="thumb" style="left:872px;background:linear-gradient(135deg,#e6e6ea,#6a4bb8)" role="img" aria-label="Purple and white striped mouthguard in a purple case"></div>
<svg class="arrow" style="left:1110px" viewBox="0 0 32 32" fill="none" stroke="#333" stroke-width="2"><circle cx="16" cy="16" r="14"/><path d="M10 16h12M17 11l5 5-5 5"/></svg>

<!-- our mouthguards -->
<section class="guards on-color">
  <h2 class="sec-title" style="top:84px">Our Mouthguards</h2>
  <div class="abs" style="left:522px;top:155px;width:155px;height:4px;background:#fff"></div>
  <p class="kicker">Protection. Comfort. Confidence.</p>
  <p class="intro">Not all mouthguards are created equal. Chemist-bought “boil and bite” guards might seem convenient, but they often provide poor fit and limited protection. A custom mouthguard, professionally fitted to your teeth and bite, offers:</p>
</section>
<div class="card" style="left:112px;top:3218px;width:278px;height:273px;border-color:#fff">
  <div class="icon" style="margin-top:22px"><svg width="50" height="54" viewBox="0 0 50 54" fill="none" stroke="#fff" stroke-width="3.5" stroke-linejoin="round"><path d="M25 5l17 7v13c0 11-8 19-17 23-9-4-17-12-17-23V12z"/><path d="M17 27l6 6 11-12"/></svg></div>
  <h3>Maximum Protection</h3>
  <p>absorbs impact and helps prevent broken teeth, jaw injuries, and concussions</p>
</div>
<div class="card" style="left:461px;top:3218px;width:278px;height:273px;border-color:#fff">
  <div class="icon" style="margin-top:22px"><svg width="54" height="54" viewBox="0 0 54 54" fill="none" stroke="#fff" stroke-width="3.5"><circle cx="25" cy="29" r="17"/><circle cx="25" cy="29" r="9"/><path d="M25 29L44 10M38 10h6v6"/></svg></div>
  <h3>Superior Comfort</h3>
  <p>fits snugly, making it easier to breathe and talk while playing</p>
</div>
<div class="card" style="left:810px;top:3218px;width:278px;height:273px;border-color:#fff">
  <div class="icon" style="margin-top:22px"><svg width="54" height="54" viewBox="0 0 54 54" fill="none" stroke="#fff" stroke-width="3.5" stroke-linejoin="round"><path d="M25 5l16 6v12c0 10-7 18-16 22-9-4-16-12-16-22V11z"/><circle cx="38" cy="38" r="8" fill="#fff"/><path d="M34 38l3 3 5-5" stroke="#0aa6d8" stroke-width="2.5"/></svg></div>
  <h3>Durability</h3>
  <p>made from high-quality dental materials that outlast off-the-shelf options</p>
</div>

<!-- footer -->
<footer class="site-footer">
  <div class="brand"><span class="brand-dot"></span><span class="brand-name" style="font-size:26px">Tandem<br>Mouthguards</span></div>
  <div class="contact-line" style="top:3814px"><svg width="20" height="26" viewBox="0 0 20 26"><path d="M10 1a9 9 0 0 0-9 9c0 7 9 15 9 15s9-8 9-15a9 9 0 0 0-9-9z" fill="var(--blue)"/><circle cx="10" cy="10" r="3.5" fill="#fff"/></svg>Unit 7, 14 Harbour Way, Kelso WA 6101</div>
  <div class="contact-line" style="top:3858px"><svg width="24" height="18" viewBox="0 0 24 18"><rect width="24" height="18" rx="2" fill="var(--blue)"/><path d="M1 2l11 8 11-8" fill="none" stroke="#fff" stroke-width="2"/></svg>hello@tandemmouthguards.example</div>
  <div class="contact-line" style="top:3898px"><svg width="22" height="22" viewBox="0 0 22 22"><path d="M5 1l4 5-2 3c1 3 3 5 6 6l3-2 5 4-3 4C9 20 2 13 1 4z" fill="var(--blue)"/></svg>(08) 5550 2718</div>

  <div class="links-title">QUICK LINKS</div>
  <div class="links-rule"></div>
  <div class="link" style="top:3787px">Home</div>
  <div class="link" style="top:3822px">About Us</div>
  <div class="link" style="top:3857px">Why Custom?</div>
  <div class="link" style="top:3892px">Gallery</div>
  <div class="link" style="top:3927px">FAQ</div>
  <div class="link" style="top:3962px">Contact / Bookings</div>

  <div class="partner" style="top:3728px;font-size:24px;color:#1e8fd6">Coastal Denture Studio</div>
  <div class="partner" style="top:3812px;font-size:42px;color:#d4143a">Nuvia</div>
  <div class="partner" style="top:3896px;font-size:46px;color:#1a7fd0">Caretta</div>
</footer>

<div class="copyright">© 2025 Tandem Mouthguards. All Rights Reserved.</div>

</body>
</html>
```